Card design for orthopaedic surgeons working as The Brightwater Joint Centre

Business cards, letterhead

Colors

Designer to choose colors to be used in the design.

Requirements
Must have
• Late addition.
• Cards letterhead must have logos of
• Crestmoor Lindell College of Surgeons
• Varenwood Bone Health Association
Nice to have
• Back of card to have space for appointment time to be added by hand and some blank space for writing incidental other notes.

```html
<!DOCTYPE html>
<html lang="en">
<head>
<meta charset="UTF-8">
<title>The Brightwater Joint Centre – Business Card</title>
<link href="https://fonts.googleapis.com/css2?family=Poppins:wght@300;400;500;600&display=swap" rel="stylesheet">
<style>
  :root{
    --bg:#e9edf1;
    --navy:#0b2f49;
    --navy-deep:#082538;
    --sky:#33a3f2;
    --white:#ffffff;
    --ink:#0e2a3f;
    --badge:#5f7a90;
  }
  html,body{margin:0;padding:0;overflow:hidden;}
  body{
    width:1200px;height:960px;background:var(--bg);
    font-family:'Poppins',sans-serif;position:relative;
  }
  .card{
    position:absolute;width:600px;height:345px;border-radius:22px;
    overflow:hidden;box-shadow:0 10px 30px rgba(10,30,50,.18);
  }
  /* Back of card */
  .card-back{
    left:90px;top:110px;
    background:linear-gradient(135deg,var(--navy) 0%,var(--navy-deep) 100%);
  }
  .card-back .brand{
    position:absolute;left:0;right:0;top:140px;text-align:center;
    color:var(--white);font-weight:300;font-size:30px;letter-spacing:.2px;
  }
  .card-back .website{
    position:absolute;left:0;right:0;bottom:58px;text-align:center;
    color:var(--sky);font-weight:300;font-size:14px;
  }
  .affiliations{
    position:absolute;right:24px;bottom:22px;display:flex;gap:10px;
  }
  .affiliation-badge{
    width:26px;height:26px;border-radius:50%;background:var(--badge);opacity:.55;
  }
  /* Front of card */
  .card-front{left:510px;top:500px;background:var(--white);}
  .card-front .wave{position:absolute;inset:0;}
  .card-front .brand{
    position:absolute;left:34px;top:94px;
    color:var(--sky);font-weight:300;font-size:23px;
  }
  .holder{position:absolute;left:140px;top:148px;text-align:center;}
  .holder .name{color:var(--sky);font-weight:600;font-size:24px;line-height:1.1;}
  .holder .role{color:var(--ink);font-weight:500;font-size:13px;}
  .contact{
    position:absolute;right:24px;top:86px;text-align:right;
    color:var(--white);font-weight:300;font-size:12px;line-height:1.5;
  }
  .contact .address{margin-bottom:8px;padding-right:18px;}
  .contact .line{display:flex;justify-content:flex-end;align-items:center;gap:7px;}
  .contact .line svg{width:11px;height:11px;flex:none;}
</style>
</head>
<body>

<div class="card card-back">
  <div class="brand">The Brightwater Joint Centre</div>
  <div class="website">www.brightwaterjointcentre.com</div>
  <div class="affiliations">
    <div class="affiliation-badge" role="img" aria-label="Crestmoor Lindell College of Surgeons membership badge"></div>
    <div class="affiliation-badge" role="img" aria-label="Varenwood Bone Health Association membership badge"></div>
  </div>
</div>

<div class="card card-front">
  <svg class="wave" viewBox="0 0 600 345" width="600" height="345" aria-hidden="true">
    <path d="M600,12 C470,12 425,80 400,170 C375,262 330,300 230,306 C150,311 80,302 0,292 L0,345 L600,345 Z" fill="var(--sky)"/>
    <path d="M30,262 C150,300 300,292 352,160 C330,262 190,296 30,280 Z" fill="var(--navy)"/>
  </svg>

  <div class="brand">The Brightwater Joint Centre</div>

  <div class="holder">
    <div class="name">Daniel Hartley</div>
    <div class="role">President</div>
  </div>

  <div class="contact">
    <div class="address">412 Heron Quay Rd<br>Lakeview, OR 97630</div>
    <div class="line">555-214-7730
      <svg viewBox="0 0 12 12"><path d="M2.5 1 L4.5 1 L5.3 3.6 L4 4.5 C4.6 6 6 7.4 7.5 8 L8.4 6.7 L11 7.5 L11 9.5 C11 10.3 10.3 11 9.5 11 C5 11 1 7 1 2.5 C1 1.7 1.7 1 2.5 1 Z" fill="#fff"/></svg>
    </div>
    <div class="line">555-318-6642
      <svg viewBox="0 0 12 12"><rect x="3" y="0.5" width="6" height="11" rx="1" fill="none" stroke="#fff"/><circle cx="6" cy="9.6" r=".7" fill="#fff"/></svg>
    </div>
    <div class="line">555-407-1195
      <svg viewBox="0 0 12 12"><rect x="3" y="1" width="6" height="3" fill="#fff"/><rect x="1" y="4.5" width="10" height="5" rx="1" fill="#fff"/><rect x="3" y="8" width="6" height="3" fill="#fff"/></svg>
    </div>
    <div class="line">dh@brightwaterjc.com
      <svg viewBox="0 0 12 12"><rect x="1" y="2.5" width="10" height="7" rx="1" fill="#fff"/><path d="M1.5 3 L6 6.5 L10.5 3" fill="none" stroke="var(--sky)"/></svg>
    </div>
    <div class="line">www.brightwaterjc.com
      <svg viewBox="0 0 12 12"><circle cx="6" cy="6" r="5" fill="#fff"/><path d="M1 6 H11 M6 1 C3.5 3.5 3.5 8.5 6 11 M6 1 C8.5 3.5 8.5 8.5 6 11" fill="none" stroke="var(--sky)" stroke-width=".8"/></svg>
    </div>
  </div>
</div>

</body>
</html>
```